Vexlorn

I have a web site VEXLORN.com that is in serious need of a re-design. The site is mean't to be a portal for an app that I have called VEXLORN which you can see in the app store or googleplay. Take a look and see what you can do.
Updates

Project Deadline Extended
Reason: Still working with designers. The "look" is not quite there but a lot of progress has been made. RB

Industry/Entity Type

Store

```html
<!DOCTYPE html>
<html lang="en">
<head>
<meta charset="utf-8">
<title>Vexlorn</title>
<link href="https://fonts.googleapis.com/css2?family=Open+Sans:wght@400;600;700;800&display=swap" rel="stylesheet">
<style>
:root{
  --navy:#1c3f7a;
  --blue:#2a6fb8;
  --teal:#2fa7c9;
  --ink:#3a3a3a;
  --muted:#6b6b6b;
  --light:#f1f2f4;
  --white:#ffffff;
  --hero-dark:#15171c;
  --footer:#1d3d74;
}
*{margin:0;padding:0;box-sizing:border-box}
html,body{width:853px;height:1200px;overflow:hidden}
body{font-family:"Open Sans",Arial,sans-serif;color:var(--ink);background:var(--white)}
.page{position:relative;width:853px;height:1200px}

.site-header{height:50px;display:flex;align-items:center;justify-content:space-between;padding:0 28px 0 36px;background:var(--white);border-bottom:1px solid #e3e3e3}
.brand{display:flex;align-items:center;gap:8px;font-weight:800;font-size:22px;color:var(--navy)}
.brand-dot{width:14px;height:14px;border-radius:50%;background:var(--teal)}
.main-nav{display:flex;gap:22px}
.main-nav a{font-size:10.5px;font-weight:700;color:var(--navy);text-decoration:none;letter-spacing:.5px}

.hero{position:relative;height:400px;overflow:hidden}
.hero-art{position:absolute;inset:0;background:
  radial-gradient(ellipse at 70% 35%,#6d7684 0%,#3a4150 35%,transparent 70%),
  radial-gradient(ellipse at 85% 80%,#2b3f7a 0%,transparent 45%),
  linear-gradient(180deg,#2a2e36 0%,var(--hero-dark) 100%)}
.hero-copy{position:absolute;left:40px;top:58px;width:300px;color:var(--white)}
.hero-copy h1{font-size:13px;font-weight:700;line-height:1.35;text-transform:uppercase;letter-spacing:.3px}
.hero-list{list-style:none;margin:14px 0 0 6px}
.hero-list li{font-size:12px;font-weight:600;line-height:1.75;display:flex;align-items:center;gap:7px}
.hero-list li::before{content:"";width:5px;height:5px;border-radius:50%;background:var(--white)}
.download{margin-top:22px;font-size:14px;font-weight:600}
.download strong{font-weight:800}
.badges{display:flex;gap:10px;margin-top:10px}
.badge{width:116px;height:36px;border-radius:6px;background:#000;border:1px solid #888}

.feature{position:relative;display:flex;padding:0 40px;overflow:hidden}
.feature-watch{height:245px;background:var(--white)}
.feature-fantasy{height:230px;background:var(--light)}
.feature-hassle{height:220px;background:var(--white)}

.art{flex:none;border-radius:4px}
.art-basketball{width:140px;height:205px;margin:22px 80px 0 40px;background:linear-gradient(160deg,#e3e6ea,#8e6a4a 55%,#2c5ca8)}
.art-bat{position:absolute;right:60px;top:75px;width:230px;height:80px;background:linear-gradient(90deg,#f4f4f4,#d8b27a 40%,#b88a4f 75%,#f2f2f2)}
.art-hockey{width:140px;height:185px;margin:16px 80px 0 40px;background:linear-gradient(160deg,#f2f2f2,#c8102e 50%,#1a1a1a)}

.copy{padding-top:24px}
.feature-watch .copy{width:480px}
.feature-fantasy .copy{width:440px}
.feature-hassle .copy{width:480px}
.copy h2{font-size:17px;font-weight:700;color:var(--blue);line-height:1.3}
.copy h2 strong{font-weight:800;color:var(--navy)}
.copy h3{font-size:13.5px;font-weight:700;color:var(--teal);margin-top:16px;text-transform:uppercase}
.copy p{font-size:10px;line-height:1.55;color:var(--muted);margin-top:8px}
.copy p strong{color:var(--ink)}
.fantasy-title{font-size:14px;font-weight:700;color:var(--blue);line-height:1.35;text-transform:uppercase}
.fantasy-title strong{color:var(--navy);font-weight:800}

.site-footer{position:absolute;left:0;bottom:0;width:853px;height:55px;background:var(--footer);display:flex;align-items:center;justify-content:space-between;padding:0 40px}
.site-footer .brand{color:var(--white);font-size:20px}
.social{display:flex;gap:6px}
.social span{width:18px;height:18px;background:var(--white);border-radius:2px}
</style>
</head>
<body>
<div class="page">
  <header class="site-header">
    <div class="brand"><span class="brand-dot"></span>Vexlorn</div>
    <nav class="main-nav">
      <a href="#">HOME</a><a href="#">ABOUT US</a><a href="#">BLOG</a><a href="#">FAQ</a><a href="#">CONTACT US</a>
    </nav>
  </header>

  <section class="hero">
    <div class="hero-art" role="img" aria-label="Stadium at night with a football player holding up a phone showing the app"></div>
    <div class="hero-copy">
      <h1>VEXLORN provides immediate access to the information you need:</h1>
      <ul class="hero-list">
        <li>Team Stats</li>
        <li>Player Stats</li>
        <li>Live Scores</li>
        <li>Schedules</li>
        <li>Past Team and Player Performance</li>
      </ul>
      <p class="download"><strong>Download</strong> it now for FREE</p>
      <div class="badges"><span class="badge"></span><span class="badge"></span></div>
    </div>
  </section>

  <section class="feature feature-watch">
    <div class="art art-basketball" role="img" aria-label="Basketball player leaping for a dunk"></div>
    <div class="copy">
      <h2>Have You Ever Been <strong>Watching a Game</strong> and You Want to Know More <strong>about a Team</strong> or <strong>Player Stats?</strong></h2>
      <p>So, you're watching a game and want to know more about a player or team? With VEXLORN you get the stats and scores in seconds, right from your phone, without missing a play.</p>
      <h3>On the Go and You Need to Know</h3>
      <p><strong>Not a problem. VEXLORN has live scores</strong> and stats for a range of sports. Download the app and you are set.</p>
    </div>
  </section>

  <section class="feature feature-fantasy">
    <div class="copy">
      <h2 class="fantasy-title">Perfect for the <strong>Fantasy Game Player</strong>. Get team and <strong>player stats</strong> from previous games this season</h2>
      <p><strong>No need to go through pages of stats from other sites.</strong> Pull up past stats fast, whether you play casual leagues or serious fantasy ones.</p>
      <h3>Get the Numbers!</h3>
      <p>Stats for pro football, college football, baseball, basketball, hockey and league soccer. More sports coming soon.</p>
    </div>
    <div class="art art-bat" role="img" aria-label="Baseball bat with a baseball"></div>
  </section>

  <section class="feature feature-hassle">
    <div class="art art-hockey" role="img" aria-label="Hockey player skating with a stick"></div>
    <div class="copy">
      <h3 style="margin-top:0">End the Hassle!</h3>
      <p>Why bother reading endless sites to find scores, player stats and past game performance? It's all in one app, ready when you are, with no clutter and no waiting around.</p>
      <h3>Sport Stats on Demand</h3>
      <p>Forget about waiting for the broadcaster to show the numbers. Just open the app, pick your team, and get the score in a matter of seconds.</p>
    </div>
  </section>

  <footer class="site-footer">
    <div class="brand"><span class="brand-dot"></span>Vexlorn</div>
    <div class="social"><span></span><span></span><span></span></div>
  </footer>
</div>
</body>
</html>
```